Plumbing & Heating company

A leaflet containing -

Company name - Larkfield Plumbing Solutions
logo
Mobile number - 07700 914062
Landline - 01632 870215
Email - Info@larkfieldplumbing.example
website - Larkfield-plumbing.example
Social media logos - insta, Facebook

services we offer

- Boiler replacements (free quote)
- General plumbing & heating
- Tap replacements
- 1st & 2nd
- New builds & Extensions
- Cylinder replcemets

```html
<!DOCTYPE html>
<html lang="en">
<head>
<meta charset="utf-8">
<title>Larkfield Plumbing Solutions – Leaflet</title>
<link href="https://fonts.googleapis.com/css2?family=Rubik:wght@700;800&family=Montserrat:wght@400;600;700&display=swap" rel="stylesheet">
<style>
  :root {
    --blue: #1a6fc0;
    --blue-deep: #0f58a8;
    --blue-light: #2a9ee0;
    --red: #ea3a3b;
    --orange: #f08a2a;
    --yellow: #f2b431;
    --ink: #222628;
    --paper: #ffffff;
    --backdrop: #ecebe8;
  }
  * { box-sizing: border-box; margin: 0; padding: 0; }
  html, body { width: 1200px; height: 1200px; overflow: hidden; background: var(--backdrop); }
  .leaflet {
    position: absolute; left: 200px; top: 45px;
    width: 800px; height: 1110px;
    background: var(--paper); overflow: hidden;
    box-shadow: 0 6px 24px rgba(0,0,0,.12);
    font-family: "Montserrat", Arial, sans-serif; color: var(--ink);
  }
  .artwork { position: absolute; inset: 0; }
  .brand {
    position: absolute; left: 55px; top: 60px;
    display: flex; align-items: center; gap: 16px;
  }
  .brand-dot { width: 54px; height: 54px; border-radius: 50%; background: var(--blue); flex: none; }
  .brand-name {
    font-family: "Rubik", Arial, sans-serif; font-weight: 800;
    font-size: 34px; line-height: 1.05; color: var(--blue);
    text-transform: uppercase; width: 300px;
  }
  .headline {
    position: absolute; left: 55px; top: 228px;
    font-family: "Rubik", Arial, sans-serif; font-weight: 800;
    font-size: 37px; line-height: 1.0; text-transform: uppercase;
  }
  .headline .red { color: var(--red); display: block; }
  .headline .blue { color: var(--blue); display: block; }
  .coverage { position: absolute; left: 57px; top: 364px; font-size: 19px; line-height: 1.3; }
  .coverage b { font-weight: 700; }
  .services-title {
    position: absolute; left: 59px; top: 446px; height: 34px;
    display: flex; align-items: center;
  }
  .services-title span {
    background: var(--blue-deep); color: #fff;
    font-family: "Rubik", Arial, sans-serif; font-weight: 700; font-size: 23px;
    padding: 0 8px; height: 34px; line-height: 34px; text-transform: uppercase;
  }
  .services-title i { width: 0; height: 0; border-left: 14px solid transparent; border-bottom: 34px solid var(--red); }
  .services { position: absolute; left: 59px; top: 500px; list-style: none; }
  .services li {
    height: 60px; display: flex; align-items: center; gap: 12px;
    font-size: 13px; font-weight: 600; text-transform: uppercase; letter-spacing: .3px;
  }
  .services svg { width: 36px; height: 36px; flex: none; }
  .quote { position: absolute; left: 56px; top: 893px; color: #fff; z-index: 2; }
  .quote p { font-weight: 700; font-size: 19px; line-height: 1.25; text-transform: uppercase; }
  .quote strong { display: block; margin-top: 6px; font-family: "Montserrat", Arial, sans-serif; font-weight: 700; font-size: 35px; letter-spacing: 1px; }
  .contacts { position: absolute; left: 56px; top: 1014px; list-style: none; z-index: 2; }
  .contacts li { display: flex; align-items: center; gap: 9px; height: 28px; font-size: 16px; }
  .contacts svg { width: 20px; height: 20px; flex: none; }
  .boiler {
    position: absolute; left: 475px; top: 337px; width: 272px; height: 437px;
    background: linear-gradient(115deg, #7e8b93 0%, #c9d1d6 55%, #eef1f3 100%);
    box-shadow: 0 4px 14px rgba(0,0,0,.25);
  }
  .plumber {
    position: absolute; left: 440px; top: 700px; width: 300px; height: 410px;
    border-radius: 150px 150px 0 0;
    background: linear-gradient(180deg, rgba(200,40,40,.85) 0%, rgba(240,210,170,.85) 40%, rgba(40,90,160,.9) 100%);
  }
</style>
</head>
<body>
<main class="leaflet">
  <svg class="artwork" viewBox="0 0 800 1110" aria-hidden="true">
    <defs>
      <linearGradient id="pipe-photo" x1="0" y1="0" x2="1" y2="1">
        <stop offset="0" stop-color="#1e72c4"/>
        <stop offset=".5" stop-color="#2f8bd6"/>
        <stop offset="1" stop-color="#1459a6"/>
      </linearGradient>
      <linearGradient id="warm-sweep" x1="0" y1="0" x2="0" y2="1">
        <stop offset="0" stop-color="#ea3a3b"/>
        <stop offset=".55" stop-color="#ee4a36"/>
        <stop offset=".8" stop-color="#f08a2a"/>
        <stop offset="1" stop-color="#f2b431"/>
      </linearGradient>
      <linearGradient id="quote-band" x1="0" y1="0" x2="1" y2="0">
        <stop offset="0" stop-color="#1668b6"/>
        <stop offset="1" stop-color="#2a9ee0"/>
      </linearGradient>
    </defs>
    <path d="M290 0 H800 V1110 H440 C400 1000 390 900 410 820 C440 700 560 560 600 420 C640 260 560 40 290 0 Z" fill="url(#pipe-photo)"/>
    <path d="M660 0 H800 V1110 H400 C380 960 420 780 520 660 C620 540 690 420 680 260 C672 150 640 60 660 0 Z" fill="#fff"/>
    <path d="M674 0 H800 V1110 H412 C392 960 432 790 530 670 C630 550 702 420 692 260 C684 150 656 60 674 0 Z" fill="url(#warm-sweep)"/>
    <path d="M0 880 H320 C380 878 420 840 450 790 C420 870 430 960 470 1040 C440 1000 400 994 340 992 H0 Z" fill="url(#quote-band)"/>
  </svg>

  <div class="boiler" role="img" aria-label="Photo of a wall-mounted combination boiler"></div>
  <div class="plumber" role="img" aria-label="Cartoon illustration of a plumber holding a large wrench and a plunger"></div>

  <div class="brand">
    <span class="brand-dot"></span>
    <span class="brand-name">Larkfield Plumbing Solutions</span>
  </div>

  <h1 class="headline">
    <span class="red">Larkfield</span>
    <span class="blue">Plumbing &amp; Heating</span>
    <span class="red">Contractor</span>
  </h1>

  <p class="coverage">Based in <b>Hampshire</b> &amp; covering<br><b>Winchester</b> &amp; the surrounding areas</p>

  <div class="services-title"><span>Services we offer</span><i></i></div>

  <ul class="services">
    <li><svg viewBox="0 0 36 36" fill="none" stroke="#1a6fc0" stroke-width="2"><rect x="4" y="8" width="12" height="20" rx="2"/><rect x="20" y="8" width="12" height="20" rx="2"/><path d="M7 14h6M23 14h6M8 32v-4M12 32v-4M24 32v-4M28 32v-4"/></svg>Boiler replacements</li>
    <li><svg viewBox="0 0 36 36" fill="none" stroke="#1a6fc0" stroke-width="4" stroke-linecap="round"><path d="M4 6h10v22h18"/></svg>General plumbing &amp; heating</li>
    <li><svg viewBox="0 0 36 36" fill="none" stroke="#1a6fc0" stroke-width="2.5" stroke-linecap="round"><path d="M6 12h14M13 12v6M4 22h22v6M26 22h6"/><circle cx="13" cy="9" r="3"/></svg>Tap replacements</li>
    <li><svg viewBox="0 0 36 36" fill="none" stroke="#1a6fc0" stroke-width="2.5"><circle cx="15" cy="15" r="6"/><path d="M15 4v4M15 22v4M4 15h4M22 15h4M7 7l3 3M20 20l3 3M7 23l3-3M20 10l3-3"/><circle cx="27" cy="27" r="6"/><path d="M24 27l2 2 4-4"/></svg>System design &amp; instlation 1st &amp; 2nd</li>
    <li><svg viewBox="0 0 36 36" fill="none" stroke="#1a6fc0" stroke-width="2.5"><rect x="5" y="6" width="24" height="24"/><path d="M5 18h24M17 6v24M29 6l4 4v20"/></svg>New builds &amp; extensions</li>
    <li><svg viewBox="0 0 36 36" fill="none" stroke="#1a6fc0" stroke-width="2.5"><circle cx="18" cy="18" r="15"/><rect x="13" y="10" width="10" height="17" rx="4"/><path d="M16 7h4"/></svg>Cylinder replcemets</li>
  </ul>

  <div class="quote">
    <p>Get a free quote for<br>boiler replacement</p>
    <strong>07700 914062</strong>
  </div>

  <ul class="contacts">
    <li><svg viewBox="0 0 20 20"><circle cx="10" cy="10" r="10" fill="#1a6fc0"/><path d="M7 5l2 3-1 1.5c.8 1.6 1.9 2.7 3.5 3.5L13 12l3 2-1 2c-4 0-9-5-9-9z" fill="#fff"/></svg>01632 870215</li>
    <li><svg viewBox="0 0 20 20"><circle cx="10" cy="10" r="10" fill="#1a6fc0"/><rect x="5" y="6.5" width="10" height="7" fill="none" stroke="#fff" stroke-width="1.4"/><path d="M5 6.5l5 4 5-4" fill="none" stroke="#fff" stroke-width="1.4"/></svg>Info@larkfieldplumbing.example</li>
    <li><svg viewBox="0 0 20 20"><circle cx="10" cy="10" r="10" fill="#1a6fc0"/><g fill="none" stroke="#fff" stroke-width="1.3"><circle cx="10" cy="10" r="6"/><ellipse cx="10" cy="10" rx="2.6" ry="6"/><path d="M4 10h12"/></g></svg>Larkfield-plumbing.example</li>
  </ul>
</main>
</body>
</html>
```